New Business card design to reflect rebrand

I would like a business card design with a good base colour for our new logo and also a placeholder for a profile pic of the card holder. the design needs to be editable to the point that we can easily change the picture of the person and use that design for printmerlo etc. we are looking at a metalic finish business card so will need a good base colour to bring out the finish.

Target Market(s)

prospective customers

Industry/Entity Type

Business

Contact Information for Business Card

I would like one editable design that we can change the name of the card holder and profile picture. The design need to be in a format that be send to printmerlo etc.

Our address is Fenwick Lodge, Copse Lane, Brampton Heath, GU14 3TP Tel no. 01483 556172

Requirements
Must have
• place holder for a profile pic for the card holder. in AI or preferably PSD format

```html
<!DOCTYPE html>
<html lang="en">
<head>
<meta charset="utf-8">
<title>Corvane Workplace Services – Business Card</title>
<link rel="stylesheet" href="https://fonts.googleapis.com/css2?family=Michroma&family=Open+Sans:wght@400&display=swap">
<style>
  :root {
    --stage-top: #2a2a2a;
    --stage-bottom: #050505;
    --card-white: #ffffff;
    --brand-orange: #ee6a00;
    --brand-navy: #2b3d57;
    --ink: #222222;
    --photo-light: #d8d4cf;
    --photo-dark: #3a3f4c;
  }
  * { margin: 0; padding: 0; box-sizing: border-box; }
  html, body { width: 1200px; height: 900px; overflow: hidden; }
  body {
    position: relative;
    background: linear-gradient(180deg, var(--stage-top) 0%, #151515 55%, var(--stage-bottom) 100%);
    font-family: "Open Sans", sans-serif;
  }
  .card {
    position: absolute;
    top: 306px;
    width: 440px;
    height: 271px;
    border-radius: 10px;
    overflow: hidden;
  }
  .card-front { left: 149px; background: var(--card-white); }
  .card-back { left: 608px; background: var(--brand-orange); }

  .profile-photo {
    position: absolute;
    left: 0;
    top: 58px;
    width: 201px;
    height: 213px;
    background: radial-gradient(ellipse at 50% 35%, var(--photo-light) 0%, #b89a84 35%, var(--photo-dark) 75%);
    border-top-right-radius: 60px 50px;
    border-top-left-radius: 60px 50px;
  }

  .holder-name {
    position: absolute;
    left: 212px;
    top: 93px;
    font-family: "Michroma", sans-serif;
    font-weight: 400;
    font-size: 14.5px;
    letter-spacing: 1px;
    white-space: nowrap;
  }
  .holder-name .first { color: var(--brand-orange); }
  .holder-name .last { color: var(--brand-navy); }

  .contact {
    position: absolute;
    left: 209px;
    top: 140px;
    font-size: 11.5px;
    line-height: 16px;
    color: var(--ink);
  }
  .contact-line { display: flex; align-items: center; gap: 4px; }
  .contact-line svg { width: 9px; height: 9px; fill: var(--brand-orange); flex: none; }
  .address { margin-top: 5px; }

  .brand-name {
    position: absolute;
    left: 0;
    right: 0;
    top: 134px;
    text-align: center;
    color: var(--card-white);
    font-family: "Michroma", sans-serif;
    font-weight: 400;
  }
  .brand-name .word {
    display: block;
    font-size: 29px;
    line-height: 34px;
    letter-spacing: 1px;
  }
  .brand-name .sub {
    display: block;
    font-size: 13px;
    line-height: 20px;
    letter-spacing: 2.5px;
  }
</style>
</head>
<body>
  <section class="card card-front" aria-label="Card front">
    <div class="profile-photo" role="img" aria-label="Profile photo of the card holder"></div>
    <h1 class="holder-name"><span class="first">DANIEL</span> <span class="last">HARPER</span></h1>
    <div class="contact">
      <p class="contact-line">
        <svg viewBox="0 0 10 10" aria-hidden="true"><path d="M1 3.5 Q5 0.5 9 3.5 L8 5 L6.5 4.2 L6.5 3.3 Q5 2.8 3.5 3.3 L3.5 4.2 L2 5 Z M2.2 5.5 H7.8 L8.5 9 H1.5 Z"/></svg>
        01483 556172
      </p>
      <p class="contact-line">
        <svg viewBox="0 0 10 10" aria-hidden="true"><path d="M0.5 2 H9.5 V8.5 H0.5 Z" /><path d="M0.8 2.3 L5 5.6 L9.2 2.3" fill="none" stroke="#fff" stroke-width="0.9"/></svg>
        info@corvane.com
      </p>
      <p class="address">Fenwick Lodge, Copse Lane,<br>Brampton Heath, GU14 3TP</p>
    </div>
  </section>

  <section class="card card-back" aria-label="Card back">
    <p class="brand-name"><span class="word">CORVANE</span><span class="sub">WORKPLACE SERVICES</span></p>
  </section>
</body>
</html>
```